Cat-products company needs smart, yet endearing, business card

We need a business card design for a new, but up-and-running, business based in Honolulu, Hawaii. The business is Purrnest Nook Co. Our first product is the most environmentally-friendly cat grass kit ever seen on the planet. Future products, currently in the R&D phase, will include a variety of exciting cat scratchers. We also do consulting work to help apartment-dwellers make their home more cat-friendly and, in the future, plan on doing full, custom installs of structure to create high walkways for cats.

Target Market(s)

Middle-aged, apartment-dwelling, middle-class workers who own 1 or more cats and who dote on them.

Industry/Entity Type

Pet Care

Contact Information for Business Card

A striking, professional, yet warm and friendly design is what we're after.

Font styles to use
Serif
Sans Serif
Other font styles liked:
• Comfortaa

Colors

Designer to choose colors to be used in the design.

Requirements
Must have
• The company logo: (see attachment)
• The company name: Purrnest Nook Co
• The web address: www.purrnestnookco.com
• Email: support@purrnestnookco.com
• Phone: +1 (808) 571 6023
• Update (Fri Jun 30 3017 7:45pm Hawaii Time) I would like, is possible, uploaded picture of the cat grass kit on the back of the card with some text along the lines of: Purrnest Nook Co - Maker Of The Leafiest Feline Sprout Set Yet
Nice to have
• A cat picture, cartoon, real or silhouette that illustrates cats in action and/or relaxing; ie using the apartment space to live, play and relax in and being well-contented.
• Most of the website is done in the font: Comfortaa. It might be nice to continue using this for brand consistency.
Should not have
• Hard-to-read fonts.

```html
<!DOCTYPE html>
<html lang="en">
<head>
<meta charset="utf-8">
<title>Purrnest Nook Co – Business Card</title>
<link rel="stylesheet" href="https://fonts.googleapis.com/css2?family=Hind:wght@600&family=Questrial&display=swap">
<style>
  :root {
    --stage: #2b2b2b;
    --paper: #f2f2f2;
    --brown: #52322a;
    --amber: #f0aa00;
    --ink: #5a5a5a;
    --white: #ffffff;
    --dot-1: #d9493c;
    --dot-2: #3b5a99;
    --dot-3: #2ba6d9;
    --dot-4: #1f7bb5;
  }
  * { box-sizing: border-box; margin: 0; padding: 0; }
  html, body {
    width: 1200px; height: 960px; overflow: hidden;
    background: var(--stage);
    font-family: "Questrial", sans-serif;
  }
  .card {
    position: absolute;
    width: 600px; height: 342px;
    border-radius: 22px;
    overflow: hidden;
  }
  /* Front */
  .card--front { left: 314px; top: 113px; background: var(--paper); }
  .front-accent {
    position: absolute; left: 422px; top: 0; width: 178px; height: 100%;
    background: var(--amber);
  }
  .front-panel {
    position: absolute; left: 294px; top: 0; width: 250px; height: 100%;
    background: var(--brown);
    display: flex; flex-direction: column; align-items: center; justify-content: center;
    gap: 18px; padding-top: 24px;
  }
  .front-brand-dot { width: 76px; height: 76px; border-radius: 50%; background: var(--amber); }
  .front-brand-name {
    font-size: 28px; line-height: 32px; color: var(--amber); text-align: center;
  }
  .holder-name {
    position: absolute; left: 36px; top: 49px;
    font-family: "Hind", sans-serif; font-weight: 600;
    font-size: 23px; line-height: 26px; color: var(--brown); letter-spacing: 0.2px;
  }
  .holder-role {
    position: absolute; left: 36px; top: 78px;
    font-size: 15px; line-height: 18px; color: var(--amber);
  }
  .contact {
    position: absolute; left: 37px;
    font-size: 15px; line-height: 18.5px; color: var(--ink);
  }
  .contact--address { top: 165px; }
  .contact--lines { top: 213px; }
  .contact b { color: var(--brown); font-weight: 700; }
  .social { position: absolute; display: flex; }
  .social span { display: block; border-radius: 50%; }
  .social--front { left: 36px; top: 281px; gap: 2px; }
  .social--front span { width: 30px; height: 30px; }
  .social span:nth-child(1) { background: var(--dot-1); }
  .social span:nth-child(2) { background: var(--dot-2); }
  .social span:nth-child(3) { background: var(--dot-3); }
  .social span:nth-child(4) { background: var(--dot-4); }
  /* Back */
  .card--back { left: 311px; top: 473px; background: var(--brown); }
  .social--back { right: 16px; top: 18px; gap: 1px; }
  .social--back span { width: 23px; height: 23px; opacity: 0.85; }
  .brand {
    position: absolute; left: 0; right: 0; top: 78px;
    display: flex; flex-direction: column; align-items: center; gap: 16px;
  }
  .brand-dot { width: 80px; height: 80px; border-radius: 50%; background: var(--white); }
  .brand-name {
    font-size: 42px; line-height: 44px; color: var(--amber); text-align: center;
  }
  .back-url {
    position: absolute; left: 0; right: 0; top: 292px; text-align: center;
    font-size: 15px; letter-spacing: 3.4px; color: var(--white);
  }
</style>
</head>
<body>
  <section class="card card--front" aria-label="Card front">
    <div class="front-accent"></div>
    <div class="front-panel">
      <span class="front-brand-dot"></span>
      <span class="front-brand-name">Purrnest<br>Nook Co</span>
    </div>
    <h1 class="holder-name">LEILANI ORTEGA</h1>
    <p class="holder-role">CEO/FOUNDER</p>
    <p class="contact contact--address">4120 Hibiscus Court<br>Honolulu, Hawaii 96815</p>
    <p class="contact contact--lines"><b>P:</b> +1 (808) 571 6023<br>support@purrnestnookco.com<br>www.purrnestnookco.com</p>
    <div class="social social--front" aria-hidden="true"><span></span><span></span><span></span><span></span></div>
  </section>

  <section class="card card--back" aria-label="Card back">
    <div class="social social--back" aria-hidden="true"><span></span><span></span><span></span><span></span></div>
    <div class="brand">
      <span class="brand-dot"></span>
      <span class="brand-name">Purrnest Nook Co</span>
    </div>
    <p class="back-url">www.purrnestnookco.com</p>
  </section>
</body>
</html>
```